Adult Literacy Program - flyer to attract volunteers and students

We want a flyer that is engaging, colorful, modern and will appeal to our primary audience of adults aged 40-60. We are trying to attract both prospective volunteers (typically age 50+, mostly women) and students (typically aged 40+).
The flyer should feature diverse people working together in pairs of two, reading or talking, with a workbook or some reading material in front of them.

Our organization trains tutors to work one-on-one with adults who are learning how to read. Most of our adult students are non-native speakers of English. Many are of Haitian or Hispanic origin, so we would like some people who represent that demographic.

The Flyer should represent reading, learning, literacy, knowledge, growth,
and opportunities.
Our students are learning to read so they can advance their job opportunities.

Target Market(s)

Adults aged 40-60, primarily women, retired, volunteers

Industry/Entity Type

Education

Font styles to use
Serif
Sans Serif

Colors

Designer to choose colors to be used in the design.

Requirements
Must have
• - UPDATE: Should be designed as a TRI-FOLD brochure on 8.5 x 11 inch paper that will be folded into thirds.
• - Images of diverse people, women and men, who look Hispanic, Haitian and other nationalities as well as Caucasian.
• - Our logo on the front cover
Nice to have
• The sample flyer is very boring and dry! We are open to different ways of presenting the text.

```html
<!DOCTYPE html>
<html lang="en">
<head>
<meta charset="utf-8">
<title>Adult Literacy Program – Tri-fold Brochure</title>
<link href="https://fonts.googleapis.com/css2?family=Open+Sans:wght@400;600&display=swap" rel="stylesheet">
<style>
  :root {
    --backdrop: #3a3a3a;
    --paper: #ffffff;
    --brand-blue: #3b7fb6;
    --text-blue: #2f6fa9;
    --magenta: #c2389b;
    --lilac: #d9c4ec;
    --photo-warm: #b98d6d;
    --photo-cool: #7d8c9c;
  }
  * { margin: 0; padding: 0; box-sizing: border-box; }
  html, body {
    width: 786px; height: 1200px; overflow: hidden;
    background: var(--backdrop);
    font-family: "Open Sans", Arial, sans-serif;
  }
  .sheet {
    position: absolute; left: 94.4px;
    width: 759px; height: 585px;
    background: var(--paper);
    transform: scale(0.8); transform-origin: top left;
    overflow: hidden;
  }
  .sheet--outside { top: 102.4px; }
  .sheet--inside { top: 601.6px; }
  .sheet__shapes { position: absolute; inset: 0; width: 759px; height: 585px; }
  .abs { position: absolute; }
  .heading { color: #fff; font-weight: 400; text-align: center; line-height: 1.22; z-index: 2; }
  .heading--stack { left: 30px; top: 12px; width: 190px; font-size: 34px; }
  .heading--tagline { left: 255px; top: 6px; width: 260px; font-size: 34px; }
  .heading--big { font-size: 47px; line-height: 1; }
  .heading--students { left: 566px; top: 66px; color: var(--text-blue); font-size: 46px; white-space: nowrap; }
  .feature-list {
    left: 27px; top: 238px; width: 175px; list-style: none;
    color: var(--text-blue); font-size: 17px; line-height: 21px;
  }
  .feature-list li::before { content: "• "; }
  .contact {
    left: 270px; top: 250px; width: 230px;
    color: var(--text-blue); font-size: 13px; line-height: 16px; text-align: center;
  }
  .contact__row { position: relative; margin-top: 16px; }
  .contact__icon { position: absolute; left: 8px; top: 1px; width: 16px; height: 16px; }
  .contact__email { margin-top: 24px; }
  .site-link { font-size: 13px; }
  .site-link--outside { left: 10px; top: 558px; color: var(--magenta); }
  .site-link--inside { left: 530px; top: 552px; width: 200px; text-align: center; color: #fff; font-size: 14px; }
  .logo-box {
    background: #fff; display: flex; align-items: center; justify-content: center; gap: 8px;
    color: var(--text-blue); font-size: 14px; font-weight: 600; text-align: center; line-height: 1.2;
  }
  .logo-box__dot { width: 12px; height: 12px; border-radius: 50%; background: var(--text-blue); flex: none; }
  .photo { border-radius: 2px; z-index: 1; }
  .photo--cloud { border-radius: 40% 40% 45% 45% / 30% 30% 55% 55%; }
  .lead { color: var(--text-blue); text-align: center; }
  .lead--title { left: 20px; top: 360px; width: 235px; font-size: 35px; line-height: 1.2; font-weight: 400; }
  .lead--sub { left: 30px; top: 410px; width: 215px; font-size: 18px; line-height: 22px; }
  .body-copy { color: var(--text-blue); font-size: 13.5px; line-height: 16px; text-align: center; }
</style>
</head>
<body>

<section class="sheet sheet--outside">
  <svg class="sheet__shapes" viewBox="0 0 759 585" aria-hidden="true">
    <path fill="var(--brand-blue)" d="M0 0 H665 Q600 100 380 110 Q290 112 262 118 Q180 185 0 178 Z"/>
    <path fill="none" stroke="var(--magenta)" stroke-width="7" d="M0 192 Q150 210 245 145"/>
    <path fill="none" stroke="var(--magenta)" stroke-width="7" d="M268 117 Q300 120 430 118 Q610 100 668 0"/>
    <path fill="var(--brand-blue)" d="M152 585 Q270 470 530 478 L540 478 Q620 410 759 412 V585 Z"/>
    <path fill="none" stroke="var(--magenta)" stroke-width="5" d="M148 585 Q265 462 528 472"/>
    <path fill="none" stroke="var(--magenta)" stroke-width="5" d="M548 452 Q640 395 759 398"/>
  </svg>

  <h1 class="abs heading heading--stack">Connect<br>Inspire<br>Enrich</h1>
  <h2 class="abs heading heading--tagline">Don’t waste a<br>moment!</h2>

  <div class="abs photo photo--cloud" role="img" aria-label="Photo of an older woman and a younger woman reading a workbook together at a table"
       style="left:488px;top:122px;width:271px;height:262px;background:linear-gradient(160deg,var(--photo-cool),var(--photo-warm) 55%,var(--magenta) 90%,var(--lilac));"></div>

  <ul class="abs feature-list">
    <li>basic literacy skills</li>
    <li>pre-GED skills</li>
    <li>conversational English</li>
    <li>Tutoring is free of charge</li>
    <li>Tutoring is one-on-one</li>
    <li>Flexible scheduling during library hours</li>
    <li>Lessons focus on student goals</li>
  </ul>

  <div class="abs contact">
    <p>Contact us today<br>to learn more.</p>
    <div class="contact__row">
      <svg class="contact__icon" viewBox="0 0 16 16"><path fill="var(--magenta)" d="M3 1 L6 4 L4.5 6 Q6 9.5 10 11.5 L12 10 L15 13 L13 15 Q4 14 1 3 Z"/></svg>
      <p>Volunteer Desk<br>555-214-0830</p>
    </div>
    <div class="contact__row">
      <svg class="contact__icon" viewBox="0 0 16 16"><path fill="var(--magenta)" d="M8 0 A5.5 5.5 0 0 1 13.5 5.5 C13.5 9 8 16 8 16 C8 16 2.5 9 2.5 5.5 A5.5 5.5 0 0 1 8 0 Z M8 3.5 A2 2 0 1 0 8 7.5 A2 2 0 1 0 8 3.5 Z"/></svg>
      <p>Harbor Glen, Millbrook &amp;<br>Cedar Bay</p>
      <svg class="contact__icon" style="top:33px" viewBox="0 0 16 16"><path fill="var(--magenta)" d="M3 1 L6 4 L4.5 6 Q6 9.5 10 11.5 L12 10 L15 13 L13 15 Q4 14 1 3 Z"/></svg>
      <p>555-214-0917</p>
    </div>
    <p class="contact__email">email: literacy@seacrestlibrary.org</p>
  </div>

  <div class="abs logo-box" style="left:333px;top:495px;width:116px;height:84px;">Seacrest County Library</div>
  <div class="abs logo-box" style="left:578px;top:453px;width:175px;height:125px;"><span class="logo-box__dot"></span>Reading Circle Friends</div>

  <p class="abs site-link site-link--outside">www.seacrestlibrary.org</p>
</section>

<section class="sheet sheet--inside">
  <svg class="sheet__shapes" viewBox="0 0 759 585" aria-hidden="true">
    <path fill="var(--brand-blue)" d="M0 0 H652 Q600 95 380 100 Q290 102 262 106 Q180 175 0 170 Z"/>
    <path fill="none" stroke="var(--magenta)" stroke-width="7" d="M0 182 Q150 198 235 140"/>
    <path fill="none" stroke="var(--magenta)" stroke-width="7" d="M266 108 Q300 112 430 110 Q590 95 632 28"/>
    <path fill="var(--brand-blue)" d="M485 585 Q560 480 759 485 V585 Z"/>
    <path fill="none" stroke="var(--magenta)" stroke-width="5" d="M528 520 Q600 470 759 472"/>
  </svg>

  <div class="abs photo" role="img" aria-label="Photo of an older volunteer tutoring a young woman at a library table"
       style="left:0;top:157px;width:253px;height:192px;background:linear-gradient(135deg,#c9b9a3,var(--photo-warm) 50%,#7a5a45);"></div>
  <div class="abs photo" role="img" aria-label="Photo of a woman and an older man reading together in front of library bookshelves"
       style="left:255px;top:166px;width:249px;height:183px;background:linear-gradient(135deg,#8c5a3f,#b88563 45%,#c0473f 80%,#6e4a36);"></div>
  <div class="abs photo photo--cloud" role="img" aria-label="Photo of a smiling older man reading a book"
       style="left:532px;top:122px;width:227px;height:206px;background:linear-gradient(170deg,#fff 5%,var(--photo-cool) 35%,var(--magenta) 75%,var(--lilac));"></div>

  <h1 class="abs heading heading--big" style="left:17px;top:52px;">Volunteer</h1>
  <h2 class="abs heading heading--big" style="left:300px;top:26px;width:160px;">Tutors</h2>
  <h2 class="abs heading heading--big heading--students">Students</h2>

  <h3 class="abs lead lead--title">Enrich a Life!</h3>
  <p class="abs lead lead--sub">Help an adult to read,<br>write or speak English</p>
  <div class="abs logo-box" style="left:60px;top:470px;width:160px;height:105px;"><span class="logo-box__dot"></span>Reading Circle Friends</div>

  <div class="abs body-copy" style="left:270px;top:366px;width:220px;">
    <p>No special skills or degrees needed — just a degree of caring!</p>
    <p>Training offered throughout the year</p>
    <p>Tutors meet students weekly at a library</p>
    <p>Instructional materials provided</p>
    <p>Ongoing support available</p>
  </div>
  <p class="abs body-copy" style="left:270px;top:534px;width:220px;line-height:21px;">Teach an adult to read and you’ll change a life forever.</p>

  <div class="abs body-copy" style="left:520px;top:400px;width:205px;">
    <p>Students are adults in need of</p>
    <p>basic literacy skills</p>
    <p>pre GED skills</p>
    <p>conversational English</p>
  </div>

  <p class="abs site-link site-link--inside">WWW.seacrestlibrary.org</p>
</section>

</body>
</html>
```